Oil Field Service company needs professional business cards

Looking to clean up our current company business cards and look a little more professional. Brenwick Casing Services is a US based company that services the oil field. We deal with engineers, managers and oil rigs....................................................................................................................................................................................................................................................................................................................................................................................................

Target Market(s)

Oil and Gas professionals

Industry/Entity Type

Oil And Gas

Contact Information for Business Card

See attached photo as example

Font styles to use
Sans Serif

Colors
ec1f27

Requirements
Must have
• Company Logo, Name, Title, Cell, Office, Fax, Email.
• See attached photo
Nice to have
• External CRT, Internal CRT, Casing Crews, Torque Turn, Laydown Machine
Should not have
• Do not introduce any new pictures and keep it professional looking

```html
<!DOCTYPE html>
<html lang="en">
<head>
<meta charset="utf-8">
<title>Brenwick Casing Services – Business Cards</title>
<link href="https://fonts.googleapis.com/css2?family=Roboto:wght@400;500;700&family=Roboto+Condensed:wght@400;500&display=swap" rel="stylesheet">
<style>
  :root{
    --red:#ec1f27;
    --red-deep:#c81a21;
    --slate:#3b5266;
    --ink:#333a40;
    --card:#f7f7f7;
    --stage:#e4e4e4;
    --white:#ffffff;
  }
  *{box-sizing:border-box;margin:0;padding:0}
  html,body{width:1200px;height:576px;overflow:hidden;background:var(--stage)}
  .stage{position:relative;width:1200px;height:576px}
  .card{position:absolute;top:139px;width:483px;height:293px;background:var(--card);border-radius:5px;box-shadow:0 3px 6px rgba(0,0,0,.18);overflow:hidden}
  .card--front{left:82px}
  .card--back{left:602px}

  /* brand name */
  .brand{position:absolute;text-align:center;color:var(--slate);font-family:"Roboto",Arial,sans-serif;font-weight:700;line-height:1}
  .brand__name{display:block;letter-spacing:1px}
  .brand__sub{display:block;letter-spacing:3px}
  .card--front .brand{left:0;right:0;top:78px}
  .card--front .brand__name{font-size:50px}
  .card--front .brand__sub{font-size:17px;margin-top:14px}
  .card--back .brand{left:262px;width:200px;top:42px}
  .card--back .brand__name{font-size:30px}
  .card--back .brand__sub{font-size:10.5px;margin-top:7px;letter-spacing:2px}

  /* front */
  .service-band{position:absolute;left:0;right:0;top:221px;height:26px;background:var(--red);color:var(--white);font-family:"Roboto",Arial,sans-serif;font-weight:500;font-size:13px;display:flex;align-items:center;justify-content:center;gap:7px;letter-spacing:.2px}
  .web-line{position:absolute;left:0;right:0;top:262px;display:flex;align-items:center;justify-content:center;gap:10px;font-family:"Roboto",Arial,sans-serif;font-size:13px;color:var(--ink)}
  .web-line::before,.web-line::after{content:"";width:66px;height:2px;background:var(--red)}

  /* back */
  .person{position:absolute;left:22px;top:32px;font-family:"Roboto Condensed",Arial,sans-serif}
  .person__name{color:var(--red);font-size:23px;font-weight:500}
  .person__title{color:var(--ink);font-family:"Roboto",Arial,sans-serif;font-size:11.5px;margin-top:3px}
  .contact{position:absolute;left:24px;top:128px;list-style:none;font-family:"Roboto Condensed",Arial,sans-serif;font-size:12.5px;color:var(--ink)}
  .contact li{display:flex;align-items:center;gap:9px;height:16px}
  .contact svg{width:10px;height:10px;fill:var(--red)}
  .wave{position:absolute;left:0;top:0;width:483px;height:293px}
  .offerings{position:absolute;right:28px;top:201px;list-style:none;text-align:right;font-family:"Roboto",Arial,sans-serif;font-weight:500;font-size:12.5px;color:var(--white);line-height:18px}
  .offerings li::after{content:" «";margin-left:4px}
</style>
</head>
<body>
<main class="stage">
  <section class="card card--front">
    <div class="brand">
      <span class="brand__name">BRENWICK</span>
      <span class="brand__sub">CASING SERVICES</span>
    </div>
    <div class="service-band">
      <span>LAYDOWN MACHINE</span><span>|</span><span>CASING CREW</span><span>|</span><span>MUD TOOL</span><span>|</span><span>TORQUE TURN</span>
    </div>
    <div class="web-line">www.brenwicksrvs.com</div>
  </section>

  <section class="card card--back">
    <svg class="wave" viewBox="0 0 483 293" aria-hidden="true">
      <path fill="var(--slate)" d="M0,236 C120,292 262,272 342,216 C402,176 452,152 483,148 L483,160 C442,166 404,186 348,226 C272,282 140,302 0,252 Z"/>
      <path fill="var(--red)" d="M0,264 C140,306 272,286 348,234 C404,194 444,174 483,170 L483,293 L0,293 Z"/>
    </svg>
    <div class="person">
      <div class="person__name">Cody Harland</div>
      <div class="person__title">Area Manager</div>
    </div>
    <div class="brand">
      <span class="brand__name">BRENWICK</span>
      <span class="brand__sub">CASING SERVICES</span>
    </div>
    <ul class="contact">
      <li><svg viewBox="0 0 10 10"><path d="M2 0 L4 2 L3 3.5 C4 5 5 6 6.5 7 L8 6 L10 8 L8.5 10 C4 9 1 6 0 1.5 Z"/></svg>(580) 555-0142</li>
      <li><svg viewBox="0 0 10 10"><path d="M0 3 C3 0 7 0 10 3 L8.5 4.5 L7 3.5 L3 3.5 L1.5 4.5 Z M2 5 L8 5 L9 10 L1 10 Z"/></svg>(580) 555-0187</li>
      <li><svg viewBox="0 0 10 10"><path d="M2.5 0 H7.5 V3 H2.5 Z M0 3.5 H10 V8 H8 V6 H2 V8 H0 Z M2.5 6.5 H7.5 V10 H2.5 Z"/></svg>(580) 555-0163</li>
      <li><svg viewBox="0 0 10 10"><path d="M5 0 C7.5 0 9 1.8 9 3.8 C9 6.5 5 10 5 10 C5 10 1 6.5 1 3.8 C1 1.8 2.5 0 5 0 Z M5 2.4 A1.5 1.5 0 1 0 5 5.4 A1.5 1.5 0 1 0 5 2.4 Z"/></svg>Redmont, OK 73850</li>
      <li><svg viewBox="0 0 10 10"><path d="M0 2 H10 L5 5.5 Z M0 3.2 L5 6.8 L10 3.2 V8.5 H0 Z"/></svg>codyharland@brenwicksrvs.com</li>
      <li><svg viewBox="0 0 10 10"><path d="M5 0 A5 5 0 1 0 5 10 A5 5 0 1 0 5 0 Z M5 1.2 A3.8 3.8 0 0 1 8.8 5 A3.8 3.8 0 0 1 5 8.8 A3.8 3.8 0 0 1 1.2 5 A3.8 3.8 0 0 1 5 1.2 Z M1 4.4 H9 V5.6 H1 Z M4.4 1 H5.6 V9 H4.4 Z"/></svg>www.brenwicksrvs.com</li>
    </ul>
    <ul class="offerings">
      <li>Mud Tool</li>
      <li>Torque Turn</li>
      <li>Casing Crew</li>
      <li>Laydown Machine</li>
    </ul>
  </section>
</main>
</body>
</html>
```